Informational Site for Advanced Chemistry R&D

The company develops oxidation chemistry for air, water, fuel pollution controls. The site has been prototyped at www.velquaresearch.example. Take a look. Now, the task is to design it for eye-catching beauty with use of color, on-page scroll-driven color transition and parallax effects. Should capture the themes: high technology, wow it's beautiful, modern, uncluttered, clean urban environment.

Target Market(s)

China Environmentally Conscious Government and Industry,

Industry/Entity Type

It Company

Number of Pages Required

3 page

Font styles to use
Sans Serif

Requirements
Must have
• Parallax effects, desktop compatible, Rich, Modern, Simple, Graphic
Nice to have
• Mobile Phone Compatible
Should not have
• Flash, or anything that is slow to load or requires high bandwidth

```html
<!DOCTYPE html>
<html lang="en">
<head>
<meta charset="utf-8">
<title>Velqua Research</title>
<link href="https://fonts.googleapis.com/css2?family=Open+Sans:wght@400;600;700&display=swap" rel="stylesheet">
<style>
:root{
  --teal:#2bb3b1;
  --teal-dark:#1f9c9f;
  --blue:#1f74c4;
  --blue-dark:#15529e;
  --navy:#1d4e9a;
  --ink:#3a3a3a;
  --muted:#6f6f6f;
  --footer:#2f2f31;
  --white:#ffffff;
}
*{box-sizing:border-box;margin:0;padding:0}
html,body{width:1200px;height:3114px;overflow:hidden}
body{font-family:"Open Sans",Arial,sans-serif;color:var(--ink);background:var(--white);position:relative}
.abs{position:absolute}

/* hero */
.hero{position:absolute;left:0;top:0;width:1200px;height:592px;overflow:hidden}
.hero-photo{position:absolute;inset:0;background:linear-gradient(90deg,#5d6468 0%,#8a9094 30%,#a59a88 42%,#7f9a5c 55%,#4f7e34 75%,#8fae6f 100%)}
.logo{position:absolute;left:87px;top:21px;width:158px;height:135px;background:var(--white);box-shadow:0 2px 8px rgba(0,0,0,.15);display:flex;flex-direction:column;align-items:center;justify-content:center;gap:8px}
.logo-dot{width:46px;height:46px;border-radius:50%;background:var(--teal)}
.logo-name{font-weight:700;font-size:21px;color:var(--teal-dark)}
.search{position:absolute;left:866px;top:25px;width:245px;height:46px;display:flex;border:1px solid #d8d8d8;background:var(--white)}
.search span{flex:1;font-size:12px;color:#999;padding:13px 14px}
.search i{width:44px;background:var(--teal);display:flex;align-items:center;justify-content:center}
.nav{position:absolute;top:98px;left:690px;display:flex;gap:44px;font-size:14px;color:#444}
.nav .active{color:var(--blue);padding-bottom:6px;border-bottom:3px solid var(--teal)}
.hero-copy{position:absolute;right:85px;top:288px;width:380px;text-align:right;color:var(--white);text-shadow:0 1px 4px rgba(0,0,0,.5)}
.hero-copy .kicker{font-size:32px;font-weight:400}
.hero-copy h1{font-size:60px;font-weight:700;line-height:1.05}
.hero-copy p{font-size:13px;line-height:1.95;margin-top:14px}
.dots{position:absolute;left:556px;top:552px;display:flex;gap:6px}
.dots i{width:14px;height:14px;border-radius:50%;border:2px solid var(--white)}
.dots i:first-child{background:var(--white)}

/* section heads */
.head{position:absolute;left:0;width:1200px;display:flex;justify-content:center;align-items:center}
.head h2{font-size:25px;font-weight:700;color:#555}
.head.light h2{color:var(--white)}
.lead{position:absolute;left:200px;width:800px;text-align:center;font-size:12.5px;line-height:2.3;color:var(--muted)}
.lead.light{color:#e4f2ff}

/* about */
.feature{position:absolute;width:320px;text-align:center}
.feature .badge{width:132px;height:132px;border-radius:50%;margin:0 auto;display:flex;align-items:center;justify-content:center;border:5px solid var(--white);box-shadow:0 0 0 3px var(--blue)}
.feature h3{font-size:19px;font-weight:700;margin-top:30px;color:#444}
.feature p{font-size:12.5px;line-height:2.1;color:var(--muted);margin-top:6px;padding:0 20px}

/* oxidation */
.ox-text{position:absolute;left:87px;top:1210px;width:540px;color:var(--white);font-size:12.5px;line-height:2.1}
.ox-text p+p{margin-top:10px}
.ox-list{list-style:none;margin-top:18px}
.ox-list li{display:flex;align-items:center;gap:12px;margin-bottom:8px}
.ox-list li::before{content:"";width:12px;height:12px;border-radius:50%;border:2px solid var(--white);box-shadow:inset 0 0 0 2px var(--teal),inset 0 0 0 6px var(--white)}
.btn{position:absolute;left:87px;top:1476px;width:190px;height:48px;border-radius:24px;background:var(--navy);color:var(--white);font-weight:700;font-size:15px;display:flex;align-items:center;justify-content:center;gap:10px}
.diagram{position:absolute;left:665px;top:1184px;width:290px;height:290px;border-radius:50%;background:radial-gradient(circle,#fff6c8 0%,#ffffff 55%,#f2f2f2 100%);border:6px solid var(--white);box-shadow:0 0 18px rgba(0,0,0,.15)}

/* products */
.card{position:absolute;top:1740px;width:247px;height:311px;background:var(--white);box-shadow:0 1px 6px rgba(0,0,0,.15)}
.card .photo{margin:8px;height:172px}
.card h3{font-size:14px;font-weight:700;color:#444;margin:18px 12px 6px}
.card p{font-size:12px;line-height:1.95;color:var(--muted);margin:0 12px}
.card p b{color:var(--blue);font-weight:400}

/* solutions */
.sol{position:absolute;top:2346px;display:flex;gap:20px;width:520px}
.sol .photo{width:188px;height:156px;flex:none;border:4px solid var(--white)}
.sol h3{font-size:16px;font-weight:700;color:var(--white);margin-top:8px}
.sol p{font-size:12px;line-height:2.1;color:#e4f2ff;margin-top:6px}
.arrow{position:absolute;width:24px;height:80px}

/* partners */
.partner{position:absolute;top:2736px;width:178px;height:108px;background:var(--white);border:4px solid #f0f0f0;box-shadow:0 1px 4px rgba(0,0,0,.12);display:flex;align-items:center;justify-content:center}

/* footer */
.footer{position:absolute;left:0;top:2896px;width:1200px;height:218px;background:var(--footer);border-top:6px solid var(--teal);color:var(--white)}
.footer h4{font-size:16px;font-weight:600;position:absolute;top:36px}
.footer .small{font-size:11.5px;line-height:2;position:absolute;top:72px;color:#ddd}
.news{position:absolute;left:570px;top:76px;display:flex}
.news span{width:210px;height:40px;background:var(--white);font-size:11px;color:#888;padding:12px}
.news b{width:98px;height:40px;background:var(--teal);font-size:11px;display:flex;align-items:center;justify-content:center}
.social{position:absolute;left:940px;top:76px;display:flex;gap:10px}
.social i{width:30px;height:30px;border-radius:50%;border:2px solid var(--white)}
.copy{position:absolute;left:0;width:1200px;top:180px;text-align:center;font-size:12px;color:#ddd}
</style>
</head>
<body>

<header class="hero">
  <div class="hero-photo" role="img" aria-label="Industrial smokestacks on the left blending into bare and leafy trees and a green forest on the right"></div>
  <svg class="abs" style="left:0;top:0" width="1200" height="140" viewBox="0 0 1200 140" aria-hidden="true">
    <path d="M0 0H1200V120C1000 60 800 10 600 40S200 110 0 40Z" fill="#f7f7f7"/>
    <path d="M0 40C200 110 400 70 600 40S1000 60 1200 120" fill="none" stroke="#2bb3b1" stroke-width="4"/>
  </svg>
  <div class="logo"><span class="logo-dot"></span><span class="logo-name">Velqua</span></div>
  <div class="search"><span>SEARCH</span><i><svg width="16" height="16" viewBox="0 0 16 16"><circle cx="7" cy="7" r="5" fill="none" stroke="#fff" stroke-width="2"/><path d="M11 11l4 4" stroke="#fff" stroke-width="2"/></svg></i></div>
  <nav class="nav"><span class="active">HOME</span><span>TECHNOLOGY</span><span>PRODUCTS</span><span>CONTACT US</span></nav>
  <div class="hero-copy">
    <div class="kicker">WELCOME TO</div>
    <h1>VELQUA</h1>
    <p>Desulfurization and denitrification using our proprietary flue gas advanced oxidation catalytic process (FGROC). Sulfur and nitrogen are oxidized and adsorbed into an environmentally friendly solid medium for safe removal from site.</p>
  </div>
  <div class="dots"><i></i><i></i><i></i><i></i><i></i></div>
  <svg class="abs" style="left:0;top:540px" width="1200" height="52" viewBox="0 0 1200 52" aria-hidden="true"><path d="M0 52V40C400 10 800 10 1200 40V52Z" fill="#fff"/></svg>
</header>

<div class="head" style="top:642px"><h2>ABOUT OUR COMPANY</h2></div>
<p class="lead" style="top:700px">It is a long established fact that a reader will be distracted by the readable content of a page when looking at its layout. The point of using Lorem Ipsum is that it has a more-or-less normal distribution of letters, as opposedreadable English.</p>

<div class="feature" style="left:100px;top:784px">
  <div class="badge" style="background:var(--blue)"><svg width="50" height="60" viewBox="0 0 50 60"><path d="M25 4C18 20 8 30 8 40a17 17 0 0034 0C42 30 32 20 25 4Z" fill="#fff"/></svg></div>
  <h3>WATER</h3>
  <p>It is a long established fact that a reader will be distracted by the readable content of a page when at its layout. The point of using Lorem</p>
</div>
<div class="feature" style="left:440px;top:784px">
  <div class="badge" style="background:var(--teal)"><svg width="64" height="50" viewBox="0 0 64 50"><path d="M6 16H40a8 8 0 10-8-8M6 26H54a7 7 0 11-7 7M6 36H34" fill="none" stroke="#fff" stroke-width="4" stroke-linecap="round"/></svg></div>
  <h3>AIR</h3>
  <p>It is a long established fact that a reader will be distracted by the readable content of a page when at its layout. The point of using Lorem</p>
</div>
<div class="feature" style="left:775px;top:784px">
  <div class="badge" style="background:var(--blue)"><svg width="52" height="60" viewBox="0 0 52 60"><rect x="6" y="6" width="26" height="48" rx="3" fill="#fff"/><rect x="11" y="12" width="16" height="12" fill="#1f74c4"/><path d="M32 20h8l4 6v20a4 4 0 01-8 0V34h-4" fill="none" stroke="#fff" stroke-width="4"/></svg></div>
  <h3>FUEL</h3>
  <p>It is a long established fact that a reader will be distracted by the readable content of a page when at its layout. The point of using Lorem</p>
</div>

<svg class="abs" style="left:0;top:1090px" width="1200" height="490" viewBox="0 0 1200 490" aria-hidden="true">
  <defs><linearGradient id="oxFill" x1="0" y1="0" x2="1" y2="1"><stop offset="0" stop-color="#35b6b4"/><stop offset="1" stop-color="#1f9c9f"/></linearGradient></defs>
  <path d="M0 50C300 0 600 20 900 40S1150 60 1200 40V490H0Z" fill="url(#oxFill)"/>
  <path d="M0 50C300 0 600 20 900 40S1150 60 1200 40" fill="none" stroke="#1f74c4" stroke-width="6"/>
</svg>
<div class="head light" style="top:1152px;justify-content:flex-start;left:87px;width:600px"><h2>ADVANCED OXIDATION</h2></div>
<div class="ox-text">
  <p>Advanced Oxidation refers to a variety of techniques employing the Hydroxyl Radical, an energetic, highly reactive cousin of the water molecule:</p>
  <p>Depending on what compound and whether in gaseous or liquid phase, the hydroxyl radical performs differently. Some examples are given below. In all cases, the hydroxyl radical has the ability to "incinerate" the compounds it comes into contact with.</p>
  <ul class="ox-list"><li>To add oxygen to inorganic molecules</li><li>To remove hydrogen from organic molecules</li></ul>
</div>
<div class="btn">LEARN MORE <svg width="14" height="14" viewBox="0 0 14 14"><circle cx="7" cy="7" r="6" fill="none" stroke="#fff" stroke-width="1.6"/><path d="M6 4l3 3-3 3" fill="none" stroke="#fff" stroke-width="1.6"/></svg></div>
<div class="diagram" role="img" aria-label="Chemistry diagram of the hydroxyl radical at the centre, linked to surrounding molecules it reacts with"></div>

<div class="head" style="top:1605px"><h2>OUR PRODUCTS</h2></div>
<p class="lead" style="top:1660px">It is a long established fact that a reader will be distracted by the readable content of a page when looking at its layout. The point of using Lorem Ipsum is that it has a more-or-less normal distribution of letters, as opposedreadable English.</p>

<div class="card" style="left:85px"><div class="photo" role="img" aria-label="Refinery towers and pipework" style="background:linear-gradient(160deg,#c9d2d8,#5a6670)"></div><h3>PROCESS - FGRX</h3><p>It is a long established fact that a rea der will be distracted by the readpose-dreadable English.<b>[....]</b></p></div>
<div class="card" style="left:344px"><div class="photo" role="img" aria-label="Worker handling chemical containers" style="background:linear-gradient(160deg,#9fb4c8,#2f4660)"></div><h3>PROCESS - PERX</h3><p>It is a long established fact that a rea der will be distracted by the readpose-dreadable English.<b>[....]</b></p></div>
<div class="card" style="left:604px"><div class="photo" role="img" aria-label="Factory chimneys releasing smoke under a dark sky" style="background:linear-gradient(180deg,#3a4a66,#7a8494)"></div><h3>PROCESS - PDRX</h3><p>It is a long established fact that a rea der will be distracted by the readpose-dreadable English.<b>[....]</b></p></div>
<div class="card" style="left:864px"><div class="photo" role="img" aria-label="Polluted water pouring from an outlet pipe into a stream" style="background:linear-gradient(160deg,#6f8a52,#8a6a3a)"></div><h3>PROCESS - VORX</h3><p>It is a long established fact that a rea der will be distracted by the readpose-dreadable English.<b>[....]</b></p></div>

<svg class="abs" style="left:0;top:2120px" width="1200" height="434" viewBox="0 0 1200 434" aria-hidden="true">
  <defs><linearGradient id="solFill" x1="0" y1="0" x2="0" y2="1"><stop offset="0" stop-color="#1f74c4"/><stop offset="1" stop-color="#15529e"/></linearGradient></defs>
  <path d="M0 30C300 -10 600 90 900 50S1150 10 1200 30V434H0Z" fill="url(#solFill)"/>
  <path d="M0 30C300 -10 600 90 900 50S1150 10 1200 30" fill="none" stroke="#2bb3b1" stroke-width="6"/>
</svg>
<div class="head light" style="top:2190px"><h2>OUR SOLUTIONS</h2></div>
<p class="lead light" style="top:2245px">It is a long established fact that a reader will be distracted by the readable content of a page when looking at its layout. The point of using Lorem Ipsum is that it has a more-or-less normal distribution of letters, as opposedreadable English.</p>
<svg class="arrow" style="left:40px;top:2375px" viewBox="0 0 24 80"><path d="M20 2L4 40l16 38" fill="none" stroke="#8fb8e6" stroke-width="2"/></svg>
<svg class="arrow" style="left:1140px;top:2375px" viewBox="0 0 24 80"><path d="M4 2l16 38L4 78" fill="none" stroke="#8fb8e6" stroke-width="2"/></svg>
<div class="sol" style="left:87px"><div class="photo" role="img" aria-label="Refinery towers and pipework" style="background:linear-gradient(160deg,#c9d2d8,#5a6670)"></div><div><h3>FUEL OIL DESULFURIZATION</h3><p>It is a long established fact that a reader will be distracted by the readable content of a page are Lorem Ipsum is that it has a more-or-less normal as opposedreadable English.</p></div></div>
<div class="sol" style="left:625px"><div class="photo" role="img" aria-label="Worker handling chemical containers" style="background:linear-gradient(160deg,#9fb4c8,#2f4660)"></div><div><h3>VOLATILE ORGANIC COMPUNDS</h3><p>It is a long established fact that a reader will be distracted by the readable content of a page are Lorem Ipsum is that it has a more-or-less normal as opposedreadable English.</p></div></div>

<div class="head" style="top:2590px"><h2>OUR PARTNERS</h2></div>
<p class="lead" style="top:2645px">It is a long established fact that a reader will be distracted by the readable content of a page when looking at its layout. The point of using Lorem Ipsum is that it has a more-or-less normal distribution of letters, as opposedreadable English.</p>
<svg class="arrow" style="left:40px;top:2750px" viewBox="0 0 24 80"><path d="M20 2L4 40l16 38" fill="none" stroke="#ddd" stroke-width="2"/></svg>
<svg class="arrow" style="left:1140px;top:2750px" viewBox="0 0 24 80"><path d="M4 2l16 38L4 78" fill="none" stroke="#ddd" stroke-width="2"/></svg>
<div class="partner" style="left:100px"><svg width="80" height="80"><circle cx="40" cy="40" r="36" fill="#e0553a"/></svg></div>
<div class="partner" style="left:305px"><svg width="80" height="80"><circle cx="40" cy="40" r="34" fill="none" stroke="#1f5aa6" stroke-width="4"/></svg></div>
<div class="partner" style="left:510px"><svg width="80" height="60"><rect x="10" y="10" width="60" height="40" rx="6" fill="#2bb3b1"/></svg></div>
<div class="partner" style="left:715px"><svg width="80" height="80"><circle cx="40" cy="40" r="34" fill="#c4232b"/></svg></div>
<div class="partner" style="left:920px"><svg width="80" height="60"><rect x="10" y="10" width="60" height="40" rx="6" fill="#2bb3b1"/></svg></div>

<footer class="footer">
  <h4 style="left:97px">CONTACT US</h4>
  <div class="small" style="left:97px;width:200px">Velqua Research Harbor Falls, U.S.A.</div>
  <div class="small" style="left:328px">+1 555 014 2290<br>info@velquaresearch.example</div>
  <h4 style="left:570px">NEWSLETTER</h4>
  <div class="news"><span>Email:</span><b>SUBSCRIBE</b></div>
  <h4 style="left:940px">FOLLOW US</h4>
  <div class="social"><i></i><i></i><i></i><i></i></div>
  <div class="copy">Copyright © 2016 Velqua Research.all rights are reserved</div>
</footer>

</body>
</html>
```